Business Card Design

New business card design

Target Market(s)

Residential & Commercial Property Managers

Industry/Entity Type

Plumbing Services

Contact Information for Business Card

Name - Rowan Keddle, title - Director, Phone Number - 0431 286 517, email - rowan@tbk-plumbing.com.au, Company ABN - 73 215 904 386,

Font styles to use
Sans Serif

Colors
0054AA
0677BA
7BADD7
CADEEF
E8F1F8

```html
<!DOCTYPE html>
<html lang="en">
<head>
<meta charset="utf-8">
<title>TBK Plumbing Services – Business Card</title>
<link href="https://fonts.googleapis.com/css2?family=Raleway:wght@300;400&family=Roboto:wght@300;400&display=swap" rel="stylesheet">
<style>
  :root {
    --bg: #3a3a3a;
    --card-dark: #1c232b;
    --card-light: #ffffff;
    --ink: #1c232b;
    --ink-soft: #8a8f94;
    --blue: #00a6e8;
    --white: #ffffff;
  }
  * { margin: 0; padding: 0; box-sizing: border-box; }
  html, body {
    width: 1200px; height: 689px; overflow: hidden;
    background: var(--bg);
  }
  .stage { position: relative; width: 1200px; height: 689px; }
  .card {
    position: absolute; top: 190px;
    width: 530px; height: 303px;
    border-radius: 18px; overflow: hidden;
  }
  .card--front { left: 40px; background: var(--card-dark); }
  .card--back { left: 630px; background: var(--card-light); }

  .brand { position: absolute; font-family: "Raleway", sans-serif; font-weight: 300; }
  .brand__name { display: block; letter-spacing: 2px; line-height: 1; }
  .brand__tag { display: block; letter-spacing: 7px; text-transform: lowercase; }
  .brand__dot {
    display: inline-block; border-radius: 50%; background: var(--blue);
    vertical-align: middle;
  }

  .card--front .brand { left: 0; right: 0; top: 92px; text-align: center; color: var(--white); }
  .card--front .brand__name { font-size: 86px; }
  .card--front .brand__tag { font-size: 13px; margin-top: 12px; }
  .card--front .brand__dot { width: 16px; height: 16px; margin-left: 6px; }

  .back-shape { position: absolute; inset: 0; }

  .card--back .brand { left: 36px; top: 70px; color: var(--ink); }
  .card--back .brand__name { font-size: 52px; }
  .card--back .brand__tag { font-size: 8px; color: var(--ink-soft); margin-top: 6px; }
  .card--back .brand__dot { width: 11px; height: 11px; margin-left: 4px; }

  .person { position: absolute; right: 40px; top: 38px; text-align: right; }
  .person__name {
    font-family: "Raleway", sans-serif; font-weight: 300;
    font-size: 24px; letter-spacing: 1px; color: var(--ink); text-transform: uppercase;
  }
  .person__title { font-family: "Roboto", sans-serif; font-size: 14px; color: var(--blue); }

  .contact {
    position: absolute; left: 36px; top: 162px;
    font-family: "Roboto", sans-serif; font-weight: 400; font-size: 13.5px;
    color: var(--ink); line-height: 1.55; list-style: none;
  }
  .contact__item { display: flex; align-items: center; gap: 7px; }
  .contact__icon { width: 13px; height: 13px; flex: none; }
  .contact__abn { margin-top: 4px; }
  .contact__label { color: var(--blue); }
</style>
</head>
<body>
<main class="stage">

  <section class="card card--front" aria-label="Card front">
    <div class="brand">
      <span class="brand__name">tbk<span class="brand__dot"></span></span>
      <span class="brand__tag">plumbing services</span>
    </div>
  </section>

  <section class="card card--back" aria-label="Card back">
    <svg class="back-shape" viewBox="0 0 530 303" preserveAspectRatio="none" aria-hidden="true">
      <path d="M0 303 L0 268 C190 245 390 190 530 80 L530 303 Z" fill="var(--card-dark)"/>
      <path d="M0 258 C170 240 300 215 390 178 C300 222 170 258 0 278 Z" fill="var(--blue)"/>
    </svg>

    <div class="person">
      <p class="person__name">Rowan Keddle</p>
      <p class="person__title">Director</p>
    </div>

    <div class="brand">
      <span class="brand__name">tbk<span class="brand__dot"></span></span>
      <span class="brand__tag">plumbing services</span>
    </div>

    <ul class="contact">
      <li class="contact__item">
        <svg class="contact__icon" viewBox="0 0 24 24" aria-hidden="true"><path fill="var(--ink)" d="M6.6 10.8a15 15 0 0 0 6.6 6.6l2.2-2.2c.3-.3.7-.4 1-.2 1.1.4 2.3.6 3.6.6.6 0 1 .4 1 1V20c0 .6-.4 1-1 1A17 17 0 0 1 3 4c0-.6.4-1 1-1h3.5c.6 0 1 .4 1 1 0 1.3.2 2.5.6 3.6.1.3 0 .7-.2 1z"/></svg>
        <span>0431 286 517</span>
      </li>
      <li class="contact__item">
        <svg class="contact__icon" viewBox="0 0 24 24" aria-hidden="true"><path fill="var(--ink)" d="M2 5h20v14H2z M4 7v.5l8 5.5 8-5.5V7l-8 5.5z" fill-rule="evenodd"/></svg>
        <span>rowan@tbk-plumbing.com.au</span>
      </li>
      <li class="contact__abn"><span class="contact__label">Company ABN</span> - 73 215 904 386</li>
    </ul>
  </section>

</main>
</body>
</html>
```